MRT Property - Business Cards

Looking for a business card & general letterhead, signage etc design for our new logo.

Colours:
000a20
0056a2
00b5ef
0088ce
68cef2

Fonts:
Poppins
Karla

Please keep look and feel of new brand - example in the zip package I sent.

```html
<!DOCTYPE html>
<html lang="en">
<head>
<meta charset="UTF-8">
<title>MRT Property – Business Cards</title>
<link rel="stylesheet" href="https://fonts.googleapis.com/css2?family=Poppins:wght@400;600;700&family=Karla:wght@400;500&display=swap">
<style>
  :root {
    --navy: #000a20;
    --card-navy: #12162b;
    --blue: #0056a2;
    --sky: #00b5ef;
    --mid-blue: #0088ce;
    --light-blue: #68cef2;
    --text-grey: #4a4f5a;
    --paper: #ffffff;
    --stage: #e4e7ec;
  }
  * { box-sizing: border-box; margin: 0; padding: 0; }
  html, body { width: 1200px; height: 800px; overflow: hidden; }
  body {
    background: var(--stage);
    font-family: "Karla", sans-serif;
    position: relative;
  }
  .card {
    position: absolute;
    left: 337px;
    width: 525px;
    height: 300px;
    border-radius: 24px;
    overflow: hidden;
    box-shadow: 0 10px 30px rgba(0, 10, 32, 0.18);
  }
  .card-front {
    top: 70px;
    background: var(--card-navy);
    display: flex;
    align-items: center;
    justify-content: center;
  }
  .card-back {
    top: 420px;
    background: var(--paper);
  }
  .brand {
    display: flex;
    align-items: center;
    gap: 12px;
  }
  .brand-mark {
    border-radius: 50%;
    background: var(--mid-blue);
    flex: none;
  }
  .brand-name {
    font-family: "Poppins", sans-serif;
    font-weight: 700;
    color: var(--blue);
    white-space: nowrap;
  }
  .card-front .brand-mark { width: 34px; height: 34px; }
  .card-front .brand-name { font-size: 40px; }
  .card-back .brand {
    position: absolute;
    left: 34px;
    top: 108px;
  }
  .card-back .brand-mark { width: 22px; height: 22px; }
  .card-back .brand-name { font-size: 26px; }
  .divider {
    position: absolute;
    left: 258px;
    top: 40px;
    width: 1px;
    height: 190px;
    background: linear-gradient(to bottom, rgba(0,136,206,0), var(--mid-blue) 30%, var(--mid-blue) 70%, rgba(0,136,206,0));
  }
  .details {
    position: absolute;
    left: 282px;
    top: 40px;
    right: 20px;
  }
  .person-name {
    font-family: "Poppins", sans-serif;
    font-weight: 700;
    font-size: 15px;
    letter-spacing: 0.3px;
    color: var(--blue);
    line-height: 1.2;
  }
  .person-title {
    font-family: "Poppins", sans-serif;
    font-size: 13px;
    color: var(--sky);
    margin-bottom: 12px;
  }
  .address {
    font-size: 13px;
    color: var(--text-grey);
    line-height: 1.4;
    margin-bottom: 12px;
    font-style: normal;
  }
  .contact-list { list-style: none; }
  .contact-list li {
    display: flex;
    align-items: center;
    gap: 8px;
    font-size: 13px;
    color: var(--text-grey);
    line-height: 1.55;
  }
  .contact-list svg { width: 12px; height: 12px; flex: none; fill: var(--blue); }
  .web-line {
    position: absolute;
    left: 0;
    right: 24px;
    bottom: 26px;
    display: flex;
    align-items: center;
    gap: 10px;
  }
  .web-line .rule { height: 1px; background: var(--mid-blue); }
  .web-line .rule-short { width: 130px; }
  .web-line .rule-long { flex: 1; }
  .web-address {
    font-family: "Poppins", sans-serif;
    font-size: 13px;
    color: var(--blue);
  }
</style>
</head>
<body>

<section class="card card-front" aria-label="Card front">
  <div class="brand">
    <span class="brand-mark"></span>
    <span class="brand-name">MRT Property</span>
  </div>
</section>

<section class="card card-back" aria-label="Card back">
  <div class="brand">
    <span class="brand-mark"></span>
    <span class="brand-name">MRT Property</span>
  </div>

  <div class="divider"></div>

  <div class="details">
    <p class="person-name">DANA HOLLOWAY</p>
    <p class="person-title">Managing Director</p>
    <address class="address">4820 Birch Hollow Rd Suite<br>210 Lakewood, Ohio 44107</address>
    <ul class="contact-list">
      <li>
        <svg viewBox="0 0 24 24" aria-hidden="true"><path d="M6.6 10.8a15.1 15.1 0 0 0 6.6 6.6l2.2-2.2a1 1 0 0 1 1-.25 11.4 11.4 0 0 0 3.6.57 1 1 0 0 1 1 1V20a1 1 0 0 1-1 1A17 17 0 0 1 3 4a1 1 0 0 1 1-1h3.5a1 1 0 0 1 1 1c0 1.25.2 2.45.57 3.57a1 1 0 0 1-.25 1z"/></svg>
        555-013-2847
      </li>
      <li>
        <svg viewBox="0 0 24 24" aria-hidden="true"><path d="M7 1h10a2 2 0 0 1 2 2v18a2 2 0 0 1-2 2H7a2 2 0 0 1-2-2V3a2 2 0 0 1 2-2zm0 3v14h10V4zm5 15.5a1 1 0 1 0 0 2 1 1 0 0 0 0-2z"/></svg>
        555-019-6402
      </li>
      <li>
        <svg viewBox="0 0 24 24" aria-hidden="true"><path d="M2 5h20v14H2zm2 2v.5l8 5 8-5V7zm0 2.8V17h16V9.8l-8 5z"/></svg>
        info@mrtproperty.com
      </li>
    </ul>
  </div>

  <div class="web-line">
    <span class="rule rule-short"></span>
    <span class="web-address">www.mrtproperty.com</span>
    <span class="rule rule-long"></span>
  </div>
</section>

</body>
</html>
```